Harrowgate Care Assurance Ltd needs a business card and logo

We need a logo for documents, invoices etc and a business card to match. We are a health auditing, training and consulting company based in NZ and working in both Australia and NZ. We ensure health organisations meet all their compliance requirements and develop expertise in the health auditing sector. The design should in some way reflect either symbols for quality management in the health sector.

Target Market(s)

Health providers and those wishing to increase their capability in meeting and understanding compliance requirements

Industry/Entity Type

Business

Contact Information for Business Card

Logo plus contact details

Logo Text

Health auditing, consultancy and training

Requirements
Must have
• Name and contact details director: Marla Fenwick, mfenwick@hca-example.co.nz, PO Box 318, Warkworth, NZ, cell +6427391652

```html
<!DOCTYPE html>
<html lang="en">
<head>
<meta charset="utf-8">
<title>Harrowgate Care Assurance Ltd – Business Card</title>
<link href="https://fonts.googleapis.com/css2?family=Open+Sans:wght@400;600;700&display=swap" rel="stylesheet">
<style>
  :root {
    --backdrop: #262626;
    --brand-blue: #0a64a8;
    --brand-blue-light: #1a86cc;
    --brand-blue-deep: #075d9c;
    --ink: #2d2d2d;
    --band-dark: #333333;
    --paper: #ffffff;
  }
  * { margin: 0; padding: 0; box-sizing: border-box; }
  html, body {
    width: 1200px; height: 1001px; overflow: hidden;
    background: var(--backdrop);
    font-family: "Open Sans", sans-serif;
  }
  .card {
    position: absolute; left: 276px; width: 618px; height: 380px;
    border-radius: 14px; overflow: hidden;
  }
  .card--front {
    top: 99px;
    background: radial-gradient(ellipse 55% 60% at 50% 45%, var(--brand-blue-light) 0%, var(--brand-blue-deep) 100%);
  }
  .card--back { top: 511px; height: 379px; background: var(--paper); }

  .brand-mark { position: absolute; border-radius: 50%; }
  .card--front .brand-mark { left: 140px; top: 138px; width: 110px; height: 110px; background: var(--paper); }
  .card--back .brand-mark { left: 52px; top: 143px; width: 90px; height: 90px; background: var(--brand-blue); }

  .brand-name {
    position: absolute; font-weight: 400; text-transform: uppercase;
    font-size: 21px; line-height: 25px; letter-spacing: 1.5px;
  }
  .card--front .brand-name { left: 256px; top: 166px; color: var(--paper); }
  .card--back .brand-name { left: 150px; top: 166px; font-size: 18px; line-height: 22px; color: var(--ink); }

  .divider {
    position: absolute; left: 362px; top: 118px; width: 1.5px; height: 141px;
    background: var(--brand-blue);
  }
  .contact { position: absolute; left: 374px; top: 126px; color: var(--ink); font-size: 16px; line-height: 21px; }
  .contact__name {
    color: var(--brand-blue); font-weight: 700; font-size: 17px; letter-spacing: 1px;
    text-transform: uppercase; margin-left: 3px; margin-bottom: 12px;
  }
  .contact__line { display: flex; align-items: center; gap: 6px; }
  .contact__address { margin-bottom: 8px; }
  .contact__line svg { flex: none; }
  .band { position: absolute; left: 0; bottom: 0; }
</style>
</head>
<body>
  <section class="card card--front">
    <div class="brand-mark"></div>
    <div class="brand-name">Harrowgate Care<br>Assurance Ltd</div>
  </section>

  <section class="card card--back">
    <div class="brand-mark"></div>
    <div class="brand-name">Harrowgate Care<br>Assurance Ltd</div>
    <div class="divider"></div>
    <div class="contact">
      <p class="contact__name">Marla Fenwick</p>
      <p class="contact__address">PO Box 318,<br>Warkworth, NZ</p>
      <p class="contact__line">
        <svg width="14" height="16" viewBox="0 0 14 16" aria-hidden="true"><rect x="3" y="1" width="8" height="14" rx="1.5" fill="none" stroke="var(--brand-blue)" stroke-width="1.6"/><line x1="6" y1="12.5" x2="8" y2="12.5" stroke="var(--brand-blue)" stroke-width="1.4"/></svg>
        +6427391652
      </p>
      <p class="contact__line">
        <svg width="14" height="16" viewBox="0 0 14 16" aria-hidden="true"><rect x="0.5" y="4" width="13" height="9" fill="var(--brand-blue)"/><polyline points="0.5,4 7,9 13.5,4" fill="none" stroke="#fff" stroke-width="1.2"/></svg>
        mfenwick@hca-example.co.nz
      </p>
    </div>
    <svg class="band" width="618" height="18" viewBox="0 0 618 18" aria-hidden="true">
      <polygon points="0,0 348,0 334,18 0,18" fill="var(--brand-blue-light)"/>
      <polygon points="355,0 618,0 618,18 341,18" fill="var(--band-dark)"/>
    </svg>
  </section>
</body>
</html>
```